Tech business card design

We need an amazing business card design for our new business 'Pexla' a marketing tech startup based in Sydney, Australia. We provide an online marketplace for businesses to search and buy advertising media, connect with service providers and learn more about marketing. We wish to communicate 'cool tech', reliability and professionalism and design based around our logo.

Target Market(s)

Business Owners

Contact Information for Business Card

Name
Position
Email Address
Website
Phone Number

Font styles to use
Other font styles liked:
• Avenir & Avenir Next

Colors

Designer to choose colors to be used in the design.

```html
<!DOCTYPE html>
<html lang="en">
<head>
<meta charset="utf-8">
<title>Pexla Business Card</title>
<link rel="stylesheet" href="https://fonts.googleapis.com/css2?family=Nunito+Sans:wght@400;700;900&display=swap">
<style>
  :root {
    --navy: #0f1c4a;
    --ink: #1a2340;
    --muted: #6b6f7a;
    --white: #ffffff;
    --stage: #eceae6;
  }
  * { margin: 0; padding: 0; box-sizing: border-box; }
  html, body { width: 1200px; height: 900px; overflow: hidden; }
  body {
    background: var(--stage);
    font-family: "Nunito Sans", Arial, sans-serif;
    display: flex;
    flex-direction: column;
    align-items: center;
    justify-content: center;
    gap: 40px;
  }
  .card {
    width: 700px;
    height: 400px;
    position: relative;
    flex: none;
    box-shadow: 0 6px 18px rgba(0,0,0,0.12);
  }
  .card-front { background: var(--white); color: var(--ink); }
  .card-back {
    background: var(--navy);
    color: var(--white);
    display: flex;
    flex-direction: column;
    align-items: center;
    justify-content: center;
  }
  .holder { position: absolute; left: 56px; top: 52px; }
  .holder-name {
    font-weight: 900;
    font-size: 26px;
    letter-spacing: 0.5px;
    text-transform: uppercase;
    color: var(--ink);
  }
  .holder-role { font-size: 16px; color: var(--muted); margin-top: 2px; }
  .wordmark-front {
    position: absolute;
    right: 64px;
    top: 150px;
    font-weight: 900;
    font-size: 96px;
    line-height: 1;
    color: var(--navy);
    letter-spacing: -1px;
  }
  .contact-list {
    position: absolute;
    left: 56px;
    bottom: 52px;
    list-style: none;
    font-size: 17px;
    color: var(--muted);
  }
  .contact-list li { display: flex; align-items: center; gap: 12px; line-height: 26px; }
  .contact-icon { width: 14px; height: 14px; fill: var(--ink); flex: none; }
  .wordmark-back {
    font-weight: 900;
    font-size: 150px;
    line-height: 1;
    letter-spacing: -2px;
  }
  .back-site { font-size: 20px; margin-top: 24px; letter-spacing: 0.5px; }
</style>
</head>
<body>
  <section class="card card-front">
    <div class="holder">
      <div class="holder-name">Daniel Marsh</div>
      <div class="holder-role">Managing Director</div>
    </div>
    <div class="wordmark-front">pexla</div>
    <ul class="contact-list">
      <li>
        <svg class="contact-icon" viewBox="0 0 16 16" aria-hidden="true"><path d="M2 4c0-1 1-2 3-2h6c2 0 3 1 3 2v1h-3V4H5v1H2zM3 6h10l1 8H2z"/></svg>
        000-987-6543
      </li>
      <li>
        <svg class="contact-icon" viewBox="0 0 16 16" aria-hidden="true"><path d="M1 3h14v10H1zM2 4v1l6 4 6-4V4z" fill-rule="evenodd"/></svg>
        info@pexlamail.com
      </li>
      <li>
        <svg class="contact-icon" viewBox="0 0 16 16" aria-hidden="true"><circle cx="8" cy="8" r="7"/><path d="M1 8h14M8 1c3 3 3 11 0 14M8 1c-3 3-3 11 0 14" stroke="#fff" stroke-width="1" fill="none"/></svg>
        www.pexlamail.com
      </li>
    </ul>
  </section>
  <section class="card card-back">
    <div class="wordmark-back">pexla</div>
    <div class="back-site">www.pexlamail.com</div>
  </section>
</body>
</html>
```